Bright Harbor, LLC Business Card Design

We need a product business card designed for a new company Bright Harbor, LLC. We make and resell waterless RV cleaner, polish and protectant. It cleans and protects in a simple spray and wipe step leaving the surface protected and conditioned to repel dust, dirt, water, smudges, bugs and fingerprints while preventing fogging. Safe on acrylic, plexiglas, lexan, plastic, rubber, painted surfaces, chrome, stainless, aluminum, vinyl, leather, glass.... This is an eco-friendly green product.

We want to play off the company name to tell the consumer that the product is easy to use and associate to the nostalgics 1950's in the USA... Thinking old travel trailer with hot rod truck pulling it as the graphic, maybe the husband cleaning the truck and the wife cleaning the trailer for a Bright Harbor surface.
Updates

Just posted our newly finished logo. Need to have "Cleaner and Protectant" added to the design as well. Thanks everyone that has submitted thus far, i am working to get comments on all.

If you need a different file format, please let me know. Thank you.

Most important info, is the logo, website and the words "Cleaner" or "Clean" along "Protectant" or "Protect" the remainder is of less importance. Highlight: www.brightharborwash.example Focus is on company brand for Brighter Harbor Cleaner product: However, need a section for the following contact info: Walt Ferris (xxx) xxx-xxxx email address Would like space for QR Code if possible.

Target Market(s)

Adults in the USA between ages of 35-75 that are actively involved in the Recreational Vehicle (RV), travel trailer, and hot rod lifestyle. We are targeting the RV marked of the high end travel, 5th wheel and bus RV market. Along with hot rods, automotive and motorcycle market.

Industry/Entity Type

Travel

Requirements
Must have
• Most important info, is the logo, website and the words "Cleaner" or "Clean" along "Protectant" or "Protect" the remainder is of less importance.

Highlight:
www.brightharborwash.example

Focus is on company brand for Brighter Harbor Cleaner product: However, need a section for the following contact info:

Walt Ferris
(xxx) xxx-xxxx
email address
Nice to have
• Would like a space for a QR Code.

```html
<!DOCTYPE html>
<html lang="en">
<head>
<meta charset="utf-8">
<title>Bright Harbor, LLC — Business Card</title>
<link href="https://fonts.googleapis.com/css2?family=Exo+2:wght@400;500;800&display=swap" rel="stylesheet">
<style>
  :root {
    --page: #e9e7e3;
    --card-light: #ffffff;
    --card-mid: #e6e6e8;
    --blue-deep: #2f57c9;
    --blue-bright: #1a9be0;
    --grey-dark: #3c3c40;
    --grey-light: #8d8d92;
    --ink: #1f1f24;
    --ink-soft: #3a3a40;
  }
  * { box-sizing: border-box; margin: 0; padding: 0; }
  html, body { width: 1200px; height: 899px; overflow: hidden; }
  body {
    background: var(--page);
    font-family: "Exo 2", Arial, sans-serif;
    color: var(--ink);
    position: relative;
  }
  .card {
    position: absolute;
    left: 320px;
    width: 560px;
    height: 320px;
    background: radial-gradient(ellipse at 50% 45%, var(--card-light) 30%, var(--card-mid) 100%);
    box-shadow: 0 6px 18px rgba(0,0,0,.18);
    overflow: hidden;
  }
  .card--front { top: 100px; }
  .card--back { top: 480px; }
  .card__shapes { position: absolute; inset: 0; width: 100%; height: 100%; }
  .brand-name {
    position: absolute;
    font-weight: 800;
    text-transform: uppercase;
    letter-spacing: 1px;
    color: var(--ink);
    white-space: nowrap;
  }
  .product-line {
    position: absolute;
    font-weight: 500;
    text-transform: uppercase;
    color: var(--ink-soft);
    white-space: nowrap;
  }
  .card--front .brand-name { left: 0; right: 0; text-align: center; top: 120px; font-size: 36px; line-height: 44px; }
  .card--front .product-line { left: 0; right: 0; text-align: center; top: 168px; font-size: 12px; letter-spacing: 3px; }
  .website-line {
    position: absolute; left: 0; right: 0; top: 232px;
    text-align: center; font-size: 14px; letter-spacing: 2px; color: var(--ink-soft);
  }
  .divider {
    position: absolute; left: 258px; top: 38px; width: 1.5px; height: 250px; background: var(--ink-soft);
  }
  .card--back .brand-name { left: 272px; width: 260px; text-align: center; top: 128px; font-size: 28px; line-height: 34px; }
  .card--back .product-line { left: 272px; width: 260px; text-align: center; top: 166px; font-size: 10px; letter-spacing: 2px; }
  .contact { position: absolute; left: 40px; top: 40px; width: 210px; }
  .contact__name { font-size: 15px; font-weight: 500; letter-spacing: 1px; text-transform: uppercase; }
  .contact__role { font-size: 11px; color: var(--ink-soft); margin-top: 2px; }
  .contact__address { font-size: 11px; line-height: 1.45; margin-top: 30px; padding-left: 16px; color: var(--ink-soft); }
  .contact__list { list-style: none; margin-top: 38px; padding-left: 28px; }
  .contact__list li { display: flex; align-items: center; gap: 7px; font-size: 9.5px; line-height: 17px; color: var(--ink-soft); white-space: nowrap; }
  .contact__list svg { width: 10px; height: 10px; fill: var(--ink-soft); flex: none; }
</style>
</head>
<body>

<section class="card card--front" aria-label="Business card front">
  <svg class="card__shapes" viewBox="0 0 560 320" aria-hidden="true">
    <defs>
      <linearGradient id="blueSweepFront" x1="0" y1="0" x2="1" y2="1">
        <stop offset="0" stop-color="#2f57c9"/><stop offset="1" stop-color="#1a9be0"/>
      </linearGradient>
      <linearGradient id="greySweepFront" x1="0" y1="0" x2="1" y2="1">
        <stop offset="0" stop-color="#8d8d92"/><stop offset="1" stop-color="#3c3c40"/>
      </linearGradient>
    </defs>
    <path d="M0 0 H170 C80 35 25 120 72 232 C40 214 14 198 0 186 Z" fill="url(#blueSweepFront)"/>
    <path d="M0 250 C60 290 120 310 180 320 H0 Z" fill="url(#greySweepFront)"/>
    <path d="M560 130 C540 230 470 292 380 320 H560 Z" fill="url(#greySweepFront)"/>
  </svg>
  <div class="brand-name">Bright Harbor</div>
  <div class="product-line">Cleaner and Protectant</div>
  <div class="website-line">www.brightharborwash.example</div>
</section>

<section class="card card--back" aria-label="Business card back">
  <svg class="card__shapes" viewBox="0 0 560 320" aria-hidden="true">
    <defs>
      <linearGradient id="blueSweepBack" x1="0" y1="0" x2="1" y2="0">
        <stop offset="0" stop-color="#2f57c9"/><stop offset="1" stop-color="#1a9be0"/>
      </linearGradient>
      <linearGradient id="greySweepBack" x1="0" y1="0" x2="1" y2="1">
        <stop offset="0" stop-color="#8d8d92"/><stop offset="1" stop-color="#3c3c40"/>
      </linearGradient>
    </defs>
    <path d="M300 0 H560 V175 C550 150 548 100 530 72 C490 30 400 8 300 0 Z" fill="url(#blueSweepBack)"/>
    <path d="M560 178 C525 262 445 300 350 320 H560 Z" fill="url(#greySweepBack)"/>
    <path d="M0 268 C40 294 80 310 125 320 H0 Z" fill="url(#greySweepBack)"/>
  </svg>

  <div class="contact">
    <div class="contact__name">Walt Ferris</div>
    <div class="contact__role">Managing Director</div>
    <div class="contact__address">240.6th floor,Dock Plaza<br>Marina Road BHV</div>
    <ul class="contact__list">
      <li><svg viewBox="0 0 10 10"><path d="M2 0.5 L3.6 2.6 L2.8 3.6 C3.4 5 4.8 6.4 6.3 7.1 L7.3 6.3 L9.5 7.9 L8.3 9.5 C4.5 9.2 0.8 5.5 0.5 1.7 Z"/></svg>012 555 0147</li>
      <li><svg viewBox="0 0 10 10"><path d="M2.5 0 H7.5 V10 H2.5 Z M3.3 1 V8 H6.7 V1 Z M4.6 8.6 H5.4 V9.3 H4.6 Z"/></svg>012 555 0148</li>
      <li><svg viewBox="0 0 10 10"><path d="M2.5 0 H7 V3 H2.5 Z M1 3.5 H9 V10 H1 Z M3 5 V6 H7 V5 Z"/></svg>012 555 0149</li>
      <li><svg viewBox="0 0 10 10"><path d="M0.5 2 H9.5 V8 H0.5 Z M1.3 2.8 L5 5.5 L8.7 2.8 Z" fill-rule="evenodd"/></svg>walt@brightharbor.example</li>
      <li><svg viewBox="0 0 10 10"><circle cx="5" cy="5" r="4.5"/><path d="M0.8 5 H9.2 M5 0.5 V9.5" stroke="#fff" stroke-width="0.8"/></svg>www.brightharborwash.example</li>
    </ul>
  </div>

  <div class="divider"></div>
  <div class="brand-name">Bright Harbor</div>
  <div class="product-line">Cleaner and Protectant</div>
</section>

</body>
</html>
```